Need App for Impact Related Events

My app is to help with internal events. When you enter the prompted event code the next screen shows you everyone currently at the event. It will give you the ability to Start a conversation with someone you met at that event, or signal it is your turn to send a message. The next screen is a message thread with that person. I am looking for a design that incorporates the colors and ‘feel good’ emotion of our logo. I have pieced together a pretty good interpretation of what I’m looking for in the attached mockup by slicing and dicing designs. I also attached our logo mascot.Screens (see attached mockups)

Note 1: I do not like the picture on the screen used in screen one because it makes it seem like a dating app. I attached an alternative photo that can be used or present different ideas.

Note 2: On the login/signup screen (screen 2) I need an additional first and last name for login, you can try to fit this on one login screen or present a two step signup screen where that is presented in the second screen.

READ MOCKUP GUIDELINES UNDER Must Haves

Target Market(s)

People attending internal social impact events

Industry/Entity Type

Charity

Font styles to use
Sans Serif

Colors
86cfc6

Requirements
Must have
• Follow the screen mockups attached to project
• PLEASE READ
• I have provided a relatively close design of what I’m looking for in the mockups. Some screens need to be followed more closely to my design mockup than other. I have listed a guide below how how closely you should follow my mockup design exactly. Overall I would like to see some ideas of incorporating a few accent colors so it doesn’t appear SO Blue. I also attached some app inspiration designs I found from around the web
• Screen Mockup Guideline Follow %
• Screen 1: 65% - mostly on target, would like to see ways to make it not SO Blue and possibly creative places to add some explainer text describing the app
• Screen 2: 50% - general design idea is here, but more open
• Screen 3: 35% - a lot more room for design influence
• Screen 4: 70% - mostly on target, a little room for design influence/color scheme ideas
• Screen 5-6: 25% - a lot of room for design change/ideas/influence
• Screen 7-8: 80% - already very close to what I need, maybe open to slight sizing and color scheme ideas
• Screen 9: 15% - the most open for influence, only the general functionality of the screen is communicated here
Nice to have
• Please Read Mockup Guideline above. In large part I am looking for something to use some nice accent colors so it is not overwhelmingly blue and bring the whole design into a seamless style.
Should not have

```html
<!DOCTYPE html>
<html lang="en">
<head>
<meta charset="utf-8">
<title>Create Event</title>
<link rel="stylesheet" href="https://fonts.googleapis.com/css2?family=Mulish:wght@400;600;700;800;900&display=swap">
<style>
  :root {
    --teal: #0ccaca;
    --teal-dark: #08b9b9;
    --ink: #1f1f2b;
    --muted: #6c6c72;
    --line: #e3e3e6;
    --paper: #ffffff;
    --sun: #f5c518;
    --avatar-a: #9a8d84;
    --avatar-b: #3d3836;
  }
  * { box-sizing: border-box; margin: 0; padding: 0; }
  html, body {
    width: 675px; height: 1200px; overflow: hidden;
    background: var(--paper);
    font-family: "Mulish", sans-serif;
  }
  .screen { position: relative; width: 675px; height: 1200px; overflow: hidden; }

  .page-title {
    position: absolute; left: 30px; top: 36px;
    font-size: 50px; font-weight: 900; color: var(--ink);
    letter-spacing: 0.2px; line-height: 1.2;
  }
  .profile-avatar {
    position: absolute; left: 579px; top: 36px;
    width: 64px; height: 64px; border-radius: 50%;
    background: radial-gradient(circle at 45% 40%, var(--avatar-a), var(--avatar-b));
  }

  .field {
    position: absolute; left: 56px; width: 561px;
    border: 2px solid var(--line); border-radius: 8px;
    display: flex; align-items: center; padding: 0 26px;
    font-size: 25px; color: var(--muted); font-weight: 400;
  }
  .field-name { top: 141px; height: 73px; }
  .field-category { top: 236px; height: 72px; justify-content: space-between; }
  .field-tags { top: 643px; height: 71px; }

  .image-drop {
    position: absolute; left: 56px; top: 330px; width: 561px; height: 287px;
    border: 2px solid var(--line); border-radius: 8px;
    display: flex; align-items: center; justify-content: center;
  }

  .generate-button {
    position: absolute; left: 188px; top: 810px; width: 300px; height: 73px;
    background: var(--teal); border: none; border-radius: 6px;
    color: #fff; font-family: "Mulish", sans-serif;
    font-size: 21px; font-weight: 800; letter-spacing: 1.6px;
  }

  .tab-bar {
    position: absolute; left: 0; top: 1070px; width: 675px; height: 130px;
    background: var(--paper);
  }
  .tab-icon { position: absolute; top: 55px; width: 50px; height: 50px; display: block; }
  .tab-calendar { left: 43px; }
  .tab-chat { left: 178px; }
  .tab-alerts { left: 448px; }
  .tab-settings { left: 583px; }
  .fab-close {
    position: absolute; left: 287px; top: 12px; width: 102px; height: 102px;
    border-radius: 50%; background: var(--teal);
    display: flex; align-items: center; justify-content: center;
  }
</style>
</head>
<body>
<main class="screen">
  <h1 class="page-title">Create Event</h1>
  <div class="profile-avatar" role="img" aria-label="Profile photo of the signed-in user"></div>

  <div class="field field-name">Event Name</div>
  <div class="field field-category">
    <span>Catagory</span>
    <svg width="34" height="20" viewBox="0 0 34 20" aria-hidden="true">
      <polyline points="3,3 17,16 31,3" fill="none" stroke="var(--teal)" stroke-width="3.5" stroke-linecap="round" stroke-linejoin="round"/>
    </svg>
  </div>

  <div class="image-drop">
    <svg width="137" height="125" viewBox="0 0 137 125" aria-label="Add event image">
      <rect x="0" y="0" width="137" height="125" rx="5" fill="var(--teal)"/>
      <circle cx="57" cy="37" r="12" fill="var(--sun)"/>
      <polygon points="16,103 50,56 75,90 92,67 123,103" fill="#fff"/>
    </svg>
  </div>

  <div class="field field-tags">Tags</div>

  <button class="generate-button">GENERATE CODE</button>

  <nav class="tab-bar">
    <svg class="tab-icon tab-calendar" viewBox="0 0 50 50" aria-label="Calendar">
      <rect x="4" y="8" width="42" height="38" rx="5" fill="none" stroke="var(--teal)" stroke-width="3.5"/>
      <line x1="4" y1="18" x2="46" y2="18" stroke="var(--teal)" stroke-width="3.5"/>
      <line x1="15" y1="3" x2="15" y2="12" stroke="var(--teal)" stroke-width="3.5" stroke-linecap="round"/>
      <line x1="35" y1="3" x2="35" y2="12" stroke="var(--teal)" stroke-width="3.5" stroke-linecap="round"/>
    </svg>
    <svg class="tab-icon tab-chat" viewBox="0 0 50 50" aria-label="Messages">
      <path d="M25 7a18 18 0 1 0 9 33.6L44 43l-3-9A18 18 0 0 0 25 7z" fill="none" stroke="var(--teal)" stroke-width="3.5" stroke-linejoin="round"/>
    </svg>
    <div class="fab-close">
      <svg width="34" height="34" viewBox="0 0 34 34" aria-label="Close">
        <line x1="4" y1="4" x2="30" y2="30" stroke="#fff" stroke-width="4" stroke-linecap="round"/>
        <line x1="30" y1="4" x2="4" y2="30" stroke="#fff" stroke-width="4" stroke-linecap="round"/>
      </svg>
    </div>
    <svg class="tab-icon tab-alerts" viewBox="0 0 50 50" aria-label="Notifications">
      <path d="M12 36V22a13 13 0 0 1 26 0v14l4 4H8z" fill="none" stroke="var(--teal)" stroke-width="3.5" stroke-linejoin="round"/>
      <path d="M20 44a5 5 0 0 0 10 0" fill="none" stroke="var(--teal)" stroke-width="3.5" stroke-linecap="round"/>
      <line x1="25" y1="4" x2="25" y2="9" stroke="var(--teal)" stroke-width="3.5" stroke-linecap="round"/>
    </svg>
    <svg class="tab-icon tab-settings" viewBox="0 0 50 50" aria-label="Settings">
      <line x1="3" y1="16" x2="47" y2="16" stroke="var(--teal)" stroke-width="3.5" stroke-linecap="round"/>
      <line x1="3" y1="34" x2="47" y2="34" stroke="var(--teal)" stroke-width="3.5" stroke-linecap="round"/>
      <circle cx="33" cy="16" r="6" fill="#fff" stroke="var(--teal)" stroke-width="3.5"/>
      <circle cx="17" cy="34" r="6" fill="#fff" stroke="var(--teal)" stroke-width="3.5"/>
    </svg>
  </nav>
</main>
</body>
</html>
```